Lanternfield Drinks business cards

We need a business card design for our new logo. The company is modern, progressive, professional, yet approachable. The key products are ready to drink bottles and cans of coffee based beverages.
These cards will be a critical part of the first impression made by our sales organization, business development team, and all external facing personnel.
Card can be a vertical or horizontal orientation.

Target Market(s)

Customers, suppliers, business partners

Industry/Entity Type

Business

Contact Information for Business Card

Business cards should feature Company Name and Logo.

Font styles to use
Serif

Colors

Designer to choose colors to be used in the design.

Requirements
Must have
• Strong readability of Name, phone #, mobile number and email address.
• Job title, website url, Street Address, and other details can be secondary level readability.
Nice to have
• High impact, simplistic quality design.
• Ok to utilize the 'H in the box' separate from the company name

```html
<!DOCTYPE html>
<html lang="en">
<head>
<meta charset="utf-8">
<title>Lanternfield Drinks — Business Cards</title>
<link href="https://fonts.googleapis.com/css2?family=Cinzel:wght@600&family=Open+Sans:wght@400;600&display=swap" rel="stylesheet">
<style>
  :root {
    --stage: #000000;
    --card-light: #ececec;
    --card-dark: #575757;
    --accent: #f05a28;
    --rule: #e7b98f;
    --ink: #3a3a3a;
    --white: #ffffff;
  }
  * { margin: 0; padding: 0; box-sizing: border-box; }
  html, body { width: 1200px; height: 900px; overflow: hidden; background: var(--stage); }
  .stage { position: relative; width: 1200px; height: 900px; }
  .card { position: absolute; top: 170px; width: 347px; height: 561px; }
  .card--front { left: 259px; background: var(--card-light); }
  .card--back { left: 631px; background: var(--card-dark); }

  .brand-mark {
    position: absolute; left: 132px; top: 90px; width: 82px; height: 82px;
    background: var(--accent);
  }
  .wordmark {
    position: absolute; left: 0; width: 100%; text-align: center;
    font-family: 'Cinzel', serif; font-weight: 600; line-height: 1;
  }
  .card--front .wordmark { top: 186px; color: var(--accent); }
  .card--back .wordmark { top: 250px; color: var(--white); }
  .wordmark__main { display: block; font-size: 36px; letter-spacing: 0.5px; }
  .wordmark__sub { display: block; font-size: 15px; letter-spacing: 2px; margin-top: 8px; }

  .person {
    position: absolute; top: 320px; left: 0; width: 100%; text-align: center;
  }
  .person__name {
    font-family: 'Cinzel', serif; font-weight: 600; font-size: 21px;
    color: var(--accent); letter-spacing: 0.5px;
  }
  .person__title {
    font-family: 'Open Sans', sans-serif; font-size: 14px; color: var(--ink); margin-top: 2px;
  }
  .icon-row {
    position: absolute; left: 0; width: 100%; display: flex;
    align-items: center; justify-content: center; gap: 6px;
  }
  .icon-row::before, .icon-row::after {
    content: ""; width: 48px; height: 1px; background: var(--rule); margin: 0 4px;
  }
  .icon-row--contact { top: 377px; }
  .icon-row--address { top: 464px; }
  .icon-row--address::before, .icon-row--address::after { width: 70px; }
  .icon { width: 16px; height: 16px; display: block; }
  .contact-list {
    position: absolute; left: 0; width: 100%; text-align: center;
    font-family: 'Open Sans', sans-serif; font-size: 14px; line-height: 20px; color: var(--ink);
  }
  .contact-list--lines { top: 400px; }
  .contact-list--address { top: 486px; }

  .website {
    position: absolute; top: 502px; left: 0; width: 100%; text-align: center;
    font-family: 'Open Sans', sans-serif; font-size: 16px; letter-spacing: 1.5px; color: var(--white);
  }
</style>
</head>
<body>
<main class="stage">
  <section class="card card--front">
    <div class="brand-mark"></div>
    <div class="wordmark">
      <span class="wordmark__main">Lanternfield</span>
      <span class="wordmark__sub">Drinks</span>
    </div>

    <div class="person">
      <p class="person__name">Daniel Carter</p>
      <p class="person__title">Managing Director</p>
    </div>

    <div class="icon-row icon-row--contact">
      <svg class="icon" viewBox="0 0 16 16" aria-hidden="true">
        <rect width="16" height="16" fill="var(--accent)"/>
        <path d="M3.5 7.5 C3.5 5 12.5 5 12.5 7.5 L10.5 8 L10 6.8 H6 L5.5 8 Z" fill="#fff"/>
        <rect x="4.5" y="8.5" width="7" height="4" rx="1" fill="#fff"/>
      </svg>
      <svg class="icon" viewBox="0 0 16 16" aria-hidden="true">
        <rect width="16" height="16" fill="var(--accent)"/>
        <rect x="5" y="3" width="6" height="10" rx="1" fill="none" stroke="#fff" stroke-width="1.3"/>
        <circle cx="8" cy="11.2" r="0.7" fill="#fff"/>
      </svg>
      <svg class="icon" viewBox="0 0 16 16" aria-hidden="true">
        <rect width="16" height="16" fill="var(--accent)"/>
        <rect x="3" y="4.5" width="10" height="7" fill="#fff"/>
        <path d="M3 4.5 L8 8.5 L13 4.5" fill="none" stroke="var(--accent)" stroke-width="1"/>
      </svg>
    </div>
    <div class="contact-list contact-list--lines">
      <p>044-210 555 018</p>
      <p>044-210 555 018</p>
      <p>info@lanternfield.com</p>
    </div>

    <div class="icon-row icon-row--address">
      <svg class="icon" viewBox="0 0 16 16" aria-hidden="true">
        <rect width="16" height="16" fill="var(--accent)"/>
        <path d="M8 13.5 C5 9.5 4.5 8.5 4.5 6.8 A3.5 3.5 0 0 1 11.5 6.8 C11.5 8.5 11 9.5 8 13.5 Z" fill="#fff"/>
        <circle cx="8" cy="6.8" r="1.3" fill="var(--accent)"/>
      </svg>
    </div>
    <div class="contact-list contact-list--address">
      <p>48 Millbrook Lane, Eastgate</p>
      <p>Westmoreland, 204517.</p>
    </div>
  </section>

  <section class="card card--back">
    <div class="wordmark">
      <span class="wordmark__main">Lanternfield</span>
      <span class="wordmark__sub">Drinks</span>
    </div>
    <p class="website">WWW.LANTERNFIELD.COM</p>
  </section>
</main>
</body>
</html>
```